business card for a massage therapy practice named 'Cedar and Willow Massage Studio'

I really need a trendy, yet easy on the eyes business card to complement my logo. Ideally with some gold or rose gold foil work.

My uploaded file of the logo I have in horizontal but I have a vertical version as well. Another color that is used in the website is a blush pink here and there. I'd like to see some trendy tropical leaves in the design.

```html
<!DOCTYPE html>
<html lang="en">
<head>
<meta charset="utf-8">
<title>Cedar and Willow Massage Studio — Business Card</title>
<link href="https://fonts.googleapis.com/css2?family=Work+Sans:wght@400;500&family=Great+Vibes&display=swap" rel="stylesheet">
<style>
  :root {
    --page: #dedede;
    --card: #262626;
    --card-edge: #3a3a3a;
    --foil: #cfcfcf;
    --foil-soft: #b9b9b9;
  }
  * { box-sizing: border-box; margin: 0; padding: 0; }
  html, body { width: 1200px; height: 900px; overflow: hidden; }
  body {
    background: var(--page);
    font-family: "Work Sans", sans-serif;
    display: flex;
    flex-direction: column;
    align-items: center;
    justify-content: center;
    gap: 40px;
  }
  .card {
    width: 700px;
    height: 400px;
    background: var(--card);
    border: 1px solid var(--card-edge);
    border-radius: 4px;
    box-shadow: 0 10px 24px rgba(0,0,0,.25);
    position: relative;
    color: var(--foil);
  }
  /* back side */
  .card--back { display: flex; align-items: center; }
  .card--back .brand {
    width: 380px;
    padding-left: 70px;
    display: flex;
    align-items: center;
    gap: 16px;
  }
  .divider {
    width: 1px;
    height: 190px;
    background: var(--foil-soft);
  }
  .contact { padding-left: 36px; }
  .contact__name {
    font-family: "Great Vibes", cursive;
    font-size: 40px;
    line-height: 1;
    margin-bottom: 16px;
    color: var(--foil);
  }
  .contact__address {
    font-size: 14px;
    line-height: 1.45;
    margin-bottom: 12px;
  }
  .contact__list { list-style: none; font-size: 14px; line-height: 1.7; }
  .contact__list li { display: flex; align-items: center; gap: 10px; }
  .contact__list svg { width: 12px; height: 12px; flex: none; }
  /* brand mark */
  .brand__dot {
    width: 22px; height: 22px;
    border-radius: 50%;
    background: var(--foil);
    flex: none;
  }
  .brand__name {
    font-family: "Work Sans", sans-serif;
    font-weight: 500;
    color: var(--foil);
    letter-spacing: .06em;
    text-transform: uppercase;
    line-height: 1.3;
  }
  .card--back .brand__name { font-size: 17px; }
  /* front side */
  .card--front {
    display: flex;
    align-items: center;
    justify-content: center;
  }
  .card--front .brand { display: flex; align-items: center; gap: 24px; }
  .card--front .brand__dot { width: 40px; height: 40px; }
  .card--front .brand__name { font-size: 32px; }
</style>
</head>
<body>
  <section class="card card--back" aria-label="Card back">
    <div class="brand">
      <span class="brand__dot"></span>
      <p class="brand__name">Cedar and Willow<br>Massage Studio</p>
    </div>
    <div class="divider"></div>
    <div class="contact">
      <p class="contact__name">Marisol Vance</p>
      <p class="contact__address">2417 Alder St. suite 210,<br>Sacramento, CA 95816</p>
      <ul class="contact__list">
        <li>
          <svg viewBox="0 0 24 24" fill="currentColor" aria-hidden="true"><path d="M6.6 10.8a15 15 0 0 0 6.6 6.6l2.2-2.2a1 1 0 0 1 1-.25 11.4 11.4 0 0 0 3.6.6 1 1 0 0 1 1 1V20a1 1 0 0 1-1 1A17 17 0 0 1 3 4a1 1 0 0 1 1-1h3.5a1 1 0 0 1 1 1c0 1.25.2 2.45.6 3.6a1 1 0 0 1-.25 1z"/></svg>
          (916) 555-0147
        </li>
        <li>
          <svg viewBox="0 0 24 24" fill="none" stroke="currentColor" stroke-width="2.4" aria-hidden="true"><rect x="3" y="5" width="18" height="14" rx="1"/><path d="M3 6l9 7 9-7"/></svg>
          hello@cedarandwillow.com
        </li>
        <li>
          <svg viewBox="0 0 24 24" fill="none" stroke="currentColor" stroke-width="2.2" aria-hidden="true"><circle cx="12" cy="12" r="9"/><path d="M3 12h18M12 3c3 3 3 15 0 18M12 3c-3 3-3 15 0 18"/></svg>
          www.cedarandwillow.com
        </li>
      </ul>
    </div>
  </section>

  <section class="card card--front" aria-label="Card front">
    <div class="brand">
      <span class="brand__dot"></span>
      <p class="brand__name">Cedar and Willow<br>Massage Studio</p>
    </div>
  </section>
</body>
</html>
```